Awesome business card design needed

We need a new business card design to go with our new logo.
We are a web development agency that specialises in highly complex back-end integrations as opposed to design, our customers are retailers, hotels, hospitals and any other organisation that has a large online marketing department.
Take a look at our website - www.brenoloft.com for some inspiration.
We want our new business cards to exude class, professionalism and style.
We are likely to choose a high-end card to print them on but we want the design of the card itself to really turn heads.
We have no specific colour requirements, the logo as you will see is a turquoise colour R89 G171 B167 #59aba7 but it can also be in white if you want to make the colour of the card something different.
The information on the card should be:
Name
Position
Tel
email
Potentially a double sided card could have our web address, twitter and FB links.

```html
<!DOCTYPE html>
<html lang="en">
<head>
<meta charset="utf-8">
<title>Brenoloft Business Card</title>
<link rel="stylesheet" href="https://fonts.googleapis.com/css2?family=Arimo:wght@400;700&display=swap">
<style>
  :root {
    --teal: #59aba7;
    --card-top: #efe3c8;
    --rule: #3b3a33;
    --stage: #f2efe9;
    --white: #ffffff;
    --mark: #ffffff;
  }
  * { margin: 0; padding: 0; box-sizing: border-box; }
  html, body { width: 1200px; height: 1069px; overflow: hidden; }
  body {
    background: var(--stage);
    font-family: "Arimo", Arial, sans-serif;
    position: relative;
  }
  .card {
    position: absolute;
    width: 592px;
    height: 338px;
    border-radius: 22px 0 28px 0;
    overflow: hidden;
    background: var(--card-top);
    box-shadow: 0 6px 18px rgba(0,0,0,0.12);
  }
  .card--front { left: 153px; top: 147px; }
  .card--back { left: 441px; top: 598px; }
  .card__brand {
    height: 216px;
    display: flex;
    align-items: center;
    justify-content: center;
    color: var(--teal);
    font-weight: 700;
    font-size: 72px;
    letter-spacing: 2px;
  }
  .card__rule { height: 4px; background: var(--rule); }
  .card__band {
    height: 118px;
    background: var(--teal);
    color: var(--white);
    position: relative;
  }
  .identity {
    position: absolute;
    right: 308px;
    top: 12px;
    text-align: right;
    line-height: 1.2;
  }
  .identity__name { font-size: 20px; font-weight: 700; }
  .identity__position { font-size: 16px; margin-bottom: 8px; }
  .identity__address { font-size: 16px; }
  .band__divider {
    position: absolute;
    left: 301px;
    top: 16px;
    width: 1px;
    height: 84px;
    background: var(--white);
  }
  .contact {
    position: absolute;
    left: 314px;
    top: 16px;
    list-style: none;
    font-size: 16px;
  }
  .contact li { display: flex; align-items: center; gap: 7px; height: 26px; }
  .contact svg { width: 13px; height: 13px; }
  .follow {
    display: flex;
    align-items: center;
    justify-content: center;
    gap: 10px;
    padding-top: 24px;
    font-size: 20px;
    font-weight: 700;
  }
  .social { width: 32px; height: 32px; border-radius: 5px; background: var(--mark); opacity: 0.85; }
  .web {
    text-align: center;
    margin-top: 14px;
    font-size: 17px;
    letter-spacing: 2px;
  }
  .web strong { font-weight: 700; }
</style>
</head>
<body>
  <section class="card card--front">
    <div class="card__brand">brenoloft</div>
    <div class="card__rule"></div>
    <div class="card__band">
      <div class="identity">
        <p class="identity__name">Your Name</p>
        <p class="identity__position">Position</p>
        <p class="identity__address">Street Name, City Name<br>State Zip Code</p>
      </div>
      <div class="band__divider"></div>
      <ul class="contact">
        <li>
          <svg viewBox="0 0 16 16" aria-hidden="true"><circle cx="8" cy="8" r="7" fill="none" stroke="#fff" stroke-width="1.6"/><path d="M5 4.5l2 2-1 1.2c.6 1.2 1.3 1.9 2.4 2.4l1.2-1 2 2-1.3 1.2C7.5 12 4.2 8.7 4 5.8z" fill="#fff"/></svg>
          123-456-7890
        </li>
        <li>
          <svg viewBox="0 0 16 16" aria-hidden="true"><rect x="1" y="4" width="14" height="10" rx="1" fill="#fff"/><path d="M1.5 5l6.5 5 6.5-5" fill="none" stroke="#59aba7" stroke-width="1.4"/></svg>
          info@brenoloft.com
        </li>
        <li>
          <svg viewBox="0 0 16 16" aria-hidden="true"><circle cx="8" cy="8" r="6.5" fill="none" stroke="#fff" stroke-width="1.5"/><ellipse cx="8" cy="8" rx="2.8" ry="6.5" fill="none" stroke="#fff" stroke-width="1.2"/><path d="M1.5 8h13M2.5 5h11M2.5 11h11" stroke="#fff" stroke-width="1.1"/></svg>
          www.brenoloft.com
        </li>
      </ul>
    </div>
  </section>

  <section class="card card--back">
    <div class="card__brand">brenoloft</div>
    <div class="card__rule"></div>
    <div class="card__band">
      <div class="follow">
        Follow Us On:
        <span class="social" aria-label="Social profile"></span>
        <span class="social" aria-label="Social profile"></span>
      </div>
      <p class="web">www.<strong>brenoloft</strong>.com</p>
    </div>
  </section>
</body>
</html>
```